Meadow Paw Web Site

We have basically a start up business that I need help with. This project is just for the web site.

Our product is a frozen raw pet food that promotes weight control, less shedding, smaller stools and an overall better health. The product is in nugget form similar to what you would see in a steak shish kabob. I only share that with you in case you want to incorporate that in the design.

We have been in business for 17 years but all of our sales have been word of mouth. We are going to be launching an infomercial this summer and I need everything stated previously to be completed before we can launch the infomercial.

We need the following (6) pages:

Home:
This is where we need to have the ability to purchase our products. Our main goal is to get the consumer to purchase our product. We have our own shopping cart so we just need to allow for the insertion of that shopping cart.

Why Raw:
This will just be a page with 4-5 paragraphs and an embedded YouTube video.

How to Use:
We will need a page with a chart (4 Columns wide with 6 rows) as well as an embedded YouTube video.

Customer Success Stories:
Allow us to add these as we move forward. I need a placeholder for an image of the customers pet and a paragraph or two explaining the situation

Where to Buy:
- Online - Find a Retailer - Find a Local Distributor - Call to Order

Contact Us:
Copper Ridge Holdings, Inc.
2740 Copper Rd
Eagan, MN 55148
(800) xxx-xxxx

We need to provide links to our to be created... Facebook page, Twitter Account, Youtube Channel, Google circle, Blog
Updates

All, I have received many front page designs that look good.  Please notice in the brief that I need multiple pages built not just the home page.  

Thanks,

Dale

Reason: I need to see the rest of the pages. Thanks, Dale

Target Market(s)

Women between the ages of 30 & 60.

Industry/Entity Type

Shopping

```html
<!DOCTYPE html>
<html lang="en">
<head>
<meta charset="utf-8">
<title>Meadow Paw – Natural Raw Dog Food</title>
<link href="https://fonts.googleapis.com/css2?family=Ubuntu:wght@300;400;500;700&display=swap" rel="stylesheet">
<style>
:root{
  --orange:#cc4a00;
  --orange-btn:#d85400;
  --amber-1:#f09a00;
  --amber-2:#f8c200;
  --ink:#2a2a2a;
  --hero-ink:#3a2716;
  --dark:#26272f;
  --dark-2:#2f3039;
  --grey-bg:#efefef;
  --grey-line:#d7d7d7;
  --side-bg:#e9e9e9;
  --muted:#8b8c96;
  --white:#ffffff;
}
*{box-sizing:border-box;margin:0;padding:0}
html,body{width:778px;height:1200px;overflow:hidden}
body{background:#f4f4f4;font-family:'Ubuntu',sans-serif;color:var(--ink);position:relative}
.page{position:absolute;left:65px;top:0;width:649px;height:1200px;background:var(--white)}
.abs{position:absolute}

/* header */
.brand{left:78px;top:14px;display:flex;align-items:center;gap:8px}
.brand-mark{width:18px;height:18px;background:var(--orange);border-radius:3px}
.brand-name{font-size:21px;font-weight:700;color:var(--orange)}
.brand-tag{left:78px;top:40px;font-size:7.5px;letter-spacing:1px;color:#555;font-weight:500}
.account{left:432px;top:8px;font-size:9.5px;font-weight:500;color:#333}
.account span{margin:0 5px}
.basket{left:538px;top:0;width:163px;height:26px;background:var(--grey-bg);border-radius:0 0 4px 4px;display:flex;align-items:center;gap:6px;padding-left:6px;font-size:9.5px;font-weight:500}
.search-bar{left:386px;top:42px;width:315px;height:28px;background:var(--grey-bg);border-radius:4px}
.search-label{left:404px;top:49px;font-size:11.5px;font-weight:500;color:#333}
.search-input{left:525px;top:47px;width:150px;height:18px;background:#fff;border:1px solid #ccc;border-radius:2px;font-size:9px;color:#444;padding:3px 6px}
.search-icon{left:681px;top:49px}

/* nav */
.nav{left:78px;top:86px;width:623px;height:28px;background:var(--dark);border-radius:4px;display:flex;overflow:hidden}
.nav a{color:#fff;text-decoration:none;font-size:12px;font-weight:500;display:flex;align-items:center;justify-content:center;border-right:1px solid #6d6e75}
.nav a:last-child{border-right:none}
.nav a.active{background:var(--orange)}

/* hero */
.hero{left:78px;top:126px;width:623px;height:216px;border-radius:4px;background:linear-gradient(100deg,var(--amber-1) 0%,#f5b000 55%,var(--amber-2) 80%,#f3a200 100%)}
.hero-title{left:104px;top:154px;width:420px;font-size:36px;font-weight:300;line-height:43px;color:var(--hero-ink)}
.hero-copy{left:104px;top:245px;width:350px;font-size:11px;line-height:16.3px;color:#fff}
.hero-art{left:478px;top:130px;width:170px;height:210px;border-radius:40% 40% 10px 10px;background:radial-gradient(ellipse at 55% 45%,#f4d9b8 0%,#d98a3c 45%,rgba(240,160,0,0) 72%)}
.pager{left:621px;top:126px;width:67px;height:18px;background:#fff;border-radius:0 0 3px 3px;display:flex;justify-content:space-around;align-items:center;font-size:9.5px;font-weight:700;color:var(--orange);padding:0 5px}

/* promos */
.promo-left{left:78px;top:357px;width:387px;height:174px;background:#e9e9e9;border-radius:4px}
.promo-photo{left:78px;top:357px;width:250px;height:174px;border-radius:4px 0 0 4px;background:linear-gradient(90deg,#e0d6cc 0%,#c8a98a 35%,#d04030 60%,#e9e9e9 100%)}
.promo-title{left:285px;top:378px;font-size:40px;font-weight:700;color:#333;letter-spacing:-1px}
.promo-sub{left:285px;top:426px;font-size:20px;font-weight:500;color:#333}
.btn-read{left:342px;top:481px;width:103px;height:32px;background:var(--orange-btn);border-radius:3px;color:#fff;font-size:16px;font-weight:500;display:flex;align-items:center;justify-content:center}
.promo-right{left:477px;top:357px;width:224px;height:174px;background:linear-gradient(180deg,#f4ac10,#f6b41c);border-radius:4px}
.range{left:492px;top:366px;font-size:14px;font-weight:500;color:#3a2716}
.range b{font-size:24px;font-weight:700}
.range-art{left:486px;top:396px;width:208px;height:128px;border-radius:3px;background:linear-gradient(120deg,#8b2a10 0%,#b66a1a 35%,#4f8a2a 65%,#7a3a14 100%);opacity:.85}

/* sidebar */
.side{left:78px;top:552px;width:172px;border:1px solid var(--grey-line)}
.side-head{height:29.5px;background:var(--side-bg);border-bottom:1px solid var(--grey-line);display:flex;align-items:center;justify-content:space-between;padding:0 9px 0 11px;font-size:10.5px;font-weight:500;color:#222}
.side-head:last-child{border-bottom:none}
.toggle{width:13px;height:13px;border-radius:50%;background:#bdbdbd;color:#fff;font-size:11px;line-height:13px;text-align:center;font-weight:700}
.side-item{height:22.8px;background:#fff;border-bottom:1px solid var(--grey-line);display:flex;align-items:center;padding-left:11px;font-size:9.3px;font-weight:500;color:#333}

/* products */
.rule{top:565px;height:6px;border-top:1px solid var(--orange);border-bottom:1px solid var(--orange)}
.pp-title{left:395px;top:552px;width:178px;height:33px;background:var(--orange);border-radius:2px;color:#fff;font-size:18px;font-weight:500;display:flex;align-items:center;justify-content:center}
.card{width:131px;height:163px;border:1px solid #bdbdbd;background:#fff}
.card-head{height:23px;background:var(--dark-2);color:#fff;font-size:12.5px;font-weight:500;display:flex;align-items:center;justify-content:center}
.card-img{width:52px;height:95px;margin:10px auto 0;border-radius:2px;background:linear-gradient(180deg,#f0c21a 0%,#e9a824 60%,#c8281e 85%,#f0c21a 100%)}
.card-foot{display:flex;justify-content:space-between;align-items:center;padding:0 9px 0 13px;margin-top:8px}
.price{font-size:12px;font-weight:700;color:#333}
.price.hot{color:var(--orange-btn)}
.btn-cart{background:var(--orange-btn);color:#fff;font-size:9.5px;font-weight:500;padding:5px 7px;border-radius:2px}

/* footer */
.footer{left:65px;top:979px;width:649px;height:191px;background:var(--dark)}
.f-brand{left:100px;top:1004px;display:flex;align-items:center;gap:7px}
.f-brand .brand-mark{background:#9a9aa2}
.f-brand .brand-name{color:#d0d0d6;font-size:19px}
.f-tag{left:100px;top:1029px;font-size:7px;letter-spacing:1px;color:#aaa}
.follow{left:78px;top:1072px;font-size:14px;font-weight:500;color:#fff}
.socials{left:78px;top:1099px;display:flex;gap:2.5px}
.socials span{width:27px;height:27px;background:#e4e4e6;border-radius:3px}
.vdiv{top:995px;width:1px;height:160px;background:#3a3b45}
.f-title{top:991px;font-size:14.5px;font-weight:500;color:#fff}
.links{top:1019px;font-size:8.3px;line-height:15.6px;color:var(--muted);list-style:none}
.links li::before{content:"› "}
.avatar{left:487px;width:49px;height:49px;border-radius:50%;background:radial-gradient(circle,#d9d9db 0%,#9c9ca3 100%);border:2px solid #d0d0d4}
.avatar-name{left:487px;width:49px;text-align:center;font-size:6.5px;color:#55565f}
.bubble{left:547px;width:154px;height:60px;background:#f1f1f2;border-radius:5px;padding:7px 9px;font-size:8.6px;line-height:12.8px;color:#333}
.bubble .q{position:absolute;right:8px;bottom:0;font-size:30px;color:#d2d2d6;font-weight:700;line-height:30px}
.bottom{left:65px;top:1170px;width:649px;height:30px;background:#e4e4e4;font-size:7.8px;color:#333;padding:10px 13px}
</style>
</head>
<body>
<div class="page"></div>

<div class="abs brand"><span class="brand-mark"></span><span class="brand-name">Meadow Paw</span></div>
<div class="abs brand-tag">100% NATURAL RAW DOG FOOD</div>
<div class="abs account">My Account<span>|</span>Log In</div>
<div class="abs basket">
  <svg width="18" height="15" viewBox="0 0 18 15"><path d="M1 5h16l-2 9H3z" fill="none" stroke="#cc4a00" stroke-width="1.6"/><path d="M5 5l4-4 4 4" fill="none" stroke="#cc4a00" stroke-width="1.4"/><path d="M6 7v5M9 7v5M12 7v5" stroke="#cc4a00" stroke-width="1.2"/></svg>
  <span>Your Basket&nbsp;&nbsp; 0 items&nbsp;&nbsp; £0.00</span>
</div>
<div class="abs search-bar"></div>
<div class="abs search-label">Simply dummy text</div>
<div class="abs search-input">Search here....</div>
<svg class="abs search-icon" width="12" height="14" viewBox="0 0 12 14"><circle cx="5" cy="5" r="3.8" fill="none" stroke="#cc4a00" stroke-width="2"/><path d="M7.5 8l3 4" stroke="#cc4a00" stroke-width="2.2" stroke-linecap="round"/></svg>

<nav class="abs nav">
  <a class="active" style="width:75px">Home</a>
  <a style="width:97px">Why Raw</a>
  <a style="width:104px">How to Use</a>
  <a style="width:115px">Where to Buy</a>
  <a style="width:127px">Success Stories</a>
  <a style="width:105px">Contact Us</a>
</nav>

<div class="abs hero"></div>
<div class="abs hero-art" role="img" aria-label="Cartoon dog sitting beside a food bowl"></div>
<div class="abs pager"><span>1</span><span>2</span><span>3</span><span>4</span></div>
<h1 class="abs hero-title">Lorem Ipsum is that it has a more-or-less</h1>
<p class="abs hero-copy">There are many variations of passages of Lorem Ipsum available, but the majority have suffered alteration in some form, by injected humour, or randomised words which don't look even slightly believable.</p>

<div class="abs promo-left"></div>
<div class="abs promo-photo" role="img" aria-label="Puppy eating from a red bowl"></div>
<div class="abs promo-title">Contrary</div>
<div class="abs promo-sub">to popular belief</div>
<div class="abs btn-read">Read more</div>
<div class="abs promo-right"></div>
<div class="abs range">range of our <b>products</b></div>
<div class="abs range-art" role="img" aria-label="Range of product bags"></div>

<div class="abs side">
  <div class="side-head">Simply random text<span class="toggle">+</span></div>
  <div class="side-head">Simply random text<span class="toggle">–</span></div>
  <div class="side-item">Distracted readable</div>
  <div class="side-item">Content of a page</div>
  <div class="side-item">When looking</div>
  <div class="side-item">Point of using</div>
  <div class="side-item">Lorem Ipsum</div>
  <div class="side-item">When looking</div>
  <div class="side-head">Simply random text<span class="toggle">+</span></div>
  <div class="side-head">Simply random text<span class="toggle">+</span></div>
  <div class="side-head">Simply random text<span class="toggle">+</span></div>
  <div class="side-head">Simply random text<span class="toggle">+</span></div>
</div>

<div class="abs rule" style="left:267px;width:123px"></div>
<div class="abs rule" style="left:577px;width:124px"></div>
<div class="abs pp-title">Popular Products</div>

<div class="abs card" style="left:267px;top:602px"><div class="card-head">Product name</div><div class="card-img" role="img" aria-label="Dog food bag"></div><div class="card-foot"><span class="price">£16.49</span><span class="btn-cart">Add to Cart</span></div></div>
<div class="abs card" style="left:420px;top:602px"><div class="card-head">Product name</div><div class="card-img" role="img" aria-label="Dog food bag"></div><div class="card-foot"><span class="price">£16.49</span><span class="btn-cart">Add to Cart</span></div></div>
<div class="abs card" style="left:569px;top:602px"><div class="card-head">Product name</div><div class="card-img" role="img" aria-label="Dog food bag"></div><div class="card-foot"><span class="price">£16.49</span><span class="btn-cart">Add to Cart</span></div></div>
<div class="abs card" style="left:267px;top:783px"><div class="card-head">Product name</div><div class="card-img" role="img" aria-label="Dog food bag"></div><div class="card-foot"><span class="price">£16.49</span><span class="btn-cart">Add to Cart</span></div></div>
<div class="abs card" style="left:420px;top:783px"><div class="card-head">Product name</div><div class="card-img" role="img" aria-label="Dog food bag"></div><div class="card-foot"><span class="price">£16.49</span><span class="btn-cart">Add to Cart</span></div></div>
<div class="abs card" style="left:569px;top:783px"><div class="card-head">Product name</div><div class="card-img" role="img" aria-label="Dog food bag"></div><div class="card-foot"><span class="price hot">£16.49</span><span class="btn-cart">Add to Cart</span></div></div>

<div class="abs footer"></div>
<div class="abs f-brand"><span class="brand-mark"></span><span class="brand-name">Meadow Paw</span></div>
<div class="abs f-tag">100% NATURAL RAW DOG FOOD</div>
<div class="abs follow">Follow us</div>
<div class="abs socials"><span></span><span></span><span></span><span></span><span></span></div>
<div class="abs vdiv" style="left:244px"></div>
<div class="abs vdiv" style="left:464px"></div>

<div class="abs f-title" style="left:266px">Quick Links</div>
<ul class="abs links" style="left:269px">
  <li>Why Raw</li><li>How to Use</li><li>Where to Buy</li><li>Success Stories</li><li>Contact Us</li>
</ul>
<ul class="abs links" style="left:360px">
  <li>There are many</li><li>variations passages</li><li>Lorem available</li><li>but the majority</li><li>have suffered</li><li>alteration in some</li><li>randomised words</li>
</ul>

<div class="abs f-title" style="left:488px">What People say</div>
<div class="abs avatar" style="top:1022px" role="img" aria-label="Customer portrait"></div>
<div class="abs avatar-name" style="top:1075px">Anna</div>
<div class="abs bubble" style="top:1021px">Lorem ipsum dolor sit amet, consectetur adipiscing elit. Integer dolor orci<span class="q">”</span></div>
<div class="abs avatar" style="top:1097px" role="img" aria-label="Customer portrait"></div>
<div class="abs avatar-name" style="top:1151px">Rosa</div>
<div class="abs bubble" style="top:1097px">Lorem ipsum dolor sit amet, consectetur adipiscing elit. Integer dolor orci<span class="q">”</span></div>

<div class="abs bottom">Company Name © 2014. Privacy Policy</div>
</body>
</html>
```